Quill Press Oceania needs a website

We require a website design which will be different to the normal websites that you visit. The objective of this website will be a call to action on the last page which will link to our email address so customers can email us their quotation requirements.

An example of how we envisage the look and the pages turning is as a flip books for example: https://www.vidharbor.example/watch?v=KtLmPzQa7Rw&feature=vh.be

page 1: just has our logo on it with the tag "Specialist producing quality printed books to your deadline."

Page 2: Black Page with white text "Black and White Book"
These are produced either digitally or offset on a complete range of stocks

Page 3: Colour books (use an image of your choice) These are also produced either digitally or offset plus we have the choice of web presses for larger print runs

Page 4: Digital books We do have a minimum run of 50 books using this process so a one off Thesis is not economically viable using this process. In special circumstance the digital process can produce books more quickly then by using our offset printing process.

Page 5: Having the complete range of printing machines at our disposal enables you to make a perfectly informed choice for your special project.

Then we need a special quote button which takes them directly to our email link. On this page we also need to add: We have had 25 years' experience printing books saving customers time and money whilst guaranteeing quality

Page 6: Logo repeated from page one with name: Morgan Elsworth and mobile phone no 0487 552 314

- Must follow the brief exactly. Must have a turn page book. Clear, simple and concise with a touch of creative flare and must lead into a call for action which is there quotation. A unique button for quotation link...something out of the ordinary which makes someone want to get a quote.

- It would be nice to have 3D Logo on Page 1 & 6.
a unique button for quotation link...something that make someone eager to proceed.

Our main objective is that they should not leave our website without giving us a quote. Please make sure that the spelling is correct and we do not require clip art images. Continue the logo colours through the theme
Updates

here is another example www.vidharbor.example/watch?v=JbXo412TrGe Added Saturday, May 13, 2017

Target Market(s)

Schools, Universities, Self Publishers, Publishers, Graphic Designers, Conference Providers, Businesses, Corporations, Government.

Industry/Entity Type

Printing

Coding

Coded - Design and coding required

Number of Pages Required

5+ page

Font styles to use
Sans Serif

Colors
34a6d7
ec1f27
fbed22
9bcb3c
ffc214
6b449b

Requirements
Must have
• Must follow the brief exactly. Must have a turn page book. Clear, simple and concise with a touch of creative flare and must lead into a call for action which is there quotation. A unique button for quotation link...something out of the ordinary which makes someone want to get a quote. would like to see the colours of the logo use throughout
Nice to have
• 3D Logo on Page 1 & 6.
• a unique button for quotation link...something that make someone eager to proceed.
• Our main objective is that they should not leave our website without giving us a quote
Should not have
• Spelling mistakes, clip art, ordinary design

```html
<!DOCTYPE html>
<html lang="en">
<head>
<meta charset="utf-8">
<title>Quill Press Oceania – Special Quote</title>
<link rel="stylesheet" href="https://fonts.googleapis.com/css2?family=Catamaran:wght@400;500;600&display=swap">
<style>
  :root {
    --purple: #7552a6;
    --green: #9bcb3c;
    --blue: #1ea3d8;
    --yellow: #fbed22;
    --white: #ffffff;
  }
  * { margin: 0; padding: 0; box-sizing: border-box; }
  html, body { width: 720px; height: 1200px; overflow: hidden; background: var(--white); }
  .page {
    position: relative; width: 720px; height: 1200px; overflow: hidden;
    font-family: "Catamaran", sans-serif; background: var(--white);
  }
  .photo-mosaic { position: absolute; left: 0; top: 0; width: 720px; height: 600px; }
  .pitch {
    position: absolute; left: 80px; top: 640px; width: 592px;
    text-align: center; color: var(--purple);
    font-size: 30px; font-weight: 600; line-height: 42px;
  }
  .quote-button {
    position: absolute; left: 267px; top: 838px; width: 214px; height: 56px;
    border-radius: 28px; background: var(--green);
    display: flex; align-items: center; justify-content: center;
    color: var(--white); font-size: 20px; font-weight: 500; text-decoration: none;
  }
  .quote-button::before {
    content: ""; position: absolute; inset: 4px;
    border: 2px solid var(--white); border-radius: 24px;
  }
  .experience-band { position: absolute; left: 0; top: 1024px; width: 720px; height: 176px; }
  .experience-text {
    position: absolute; left: 100px; top: 1083px; width: 540px;
    text-align: center; color: var(--white);
    font-size: 21px; font-weight: 400; line-height: 30px; letter-spacing: 0.3px;
  }
</style>
</head>
<body>
<main class="page">
  <svg class="photo-mosaic" viewBox="0 0 720 600" aria-hidden="false">
    <defs>
      <linearGradient id="flatbedTones" x1="0" y1="0" x2="1" y2="1">
        <stop offset="0" stop-color="#2b5fd6"/>
        <stop offset="0.45" stop-color="#9aa6b8"/>
        <stop offset="1" stop-color="#3a3d45"/>
      </linearGradient>
      <linearGradient id="wideFormatTones" x1="0" y1="0" x2="1" y2="1">
        <stop offset="0" stop-color="#5c5d63"/>
        <stop offset="0.4" stop-color="#1d1a1f"/>
        <stop offset="0.65" stop-color="#2d7fc4"/>
        <stop offset="0.85" stop-color="#e98b2c"/>
        <stop offset="1" stop-color="#2a2326"/>
      </linearGradient>
      <linearGradient id="pressTones" x1="0" y1="0" x2="1" y2="1">
        <stop offset="0" stop-color="#6d6f74"/>
        <stop offset="0.5" stop-color="#b9c6d6"/>
        <stop offset="0.75" stop-color="#e0a23a"/>
        <stop offset="1" stop-color="#2f3136"/>
      </linearGradient>
    </defs>
    <g stroke-linejoin="round" stroke-width="18">
      <polygon role="img" aria-label="Photo of a flatbed colour printer in motion"
        points="120,-108 336,112 120,332 -100,112" fill="url(#flatbedTones)" stroke="url(#flatbedTones)"/>
      <polygon role="img" aria-label="Photo of a wide-format printer producing a colourful butterfly artwork"
        points="524,-28 808,256 524,540 240,256" fill="url(#wideFormatTones)" stroke="url(#wideFormatTones)"/>
      <polygon role="img" aria-label="Photo of a large printing press with colourful printed sheets"
        points="216,274 374,432 216,590 58,432" fill="url(#pressTones)" stroke="url(#pressTones)"/>
    </g>
  </svg>

  <h1 class="pitch">Having the complete range of printing machines at our disposal enables you to make a perfectly informed choice for your special project.</h1>

  <a class="quote-button" href="mailto:quotes@quillpressoceania.example">Special Quote</a>

  <svg class="experience-band" viewBox="0 0 720 176" preserveAspectRatio="none" aria-hidden="true">
    <path d="M0,50 C110,30 200,4 290,8 C330,10 355,22 376,26 C400,20 430,6 480,6 C570,6 640,28 720,40 L720,176 L0,176 Z" fill="var(--yellow)"/>
    <path d="M0,60 C110,40 200,14 290,18 C330,20 355,32 376,36 C400,30 430,16 480,16 C570,16 640,38 720,50 L720,176 L0,176 Z" fill="var(--blue)"/>
  </svg>
  <p class="experience-text">We have had 25 years' experience printing books saving customers time and money whilst guaranteeing quality</p>
</main>
</body>
</html>
```